CBD AgriBusiness Verdant Trophy Business Card

We are HiTec producer of medical cannabis CBD Switzerland of high quality. Our website is alpinleaf.net, we will also revisit it graphically, the winner of this contest will be the graphic designer chosen for the new design of the website. We stand out by the skill of the team, many of our engineers we win cup cannabis. I join the current map to take as an example but to revisit completely: deletion of surname and first name, modification of funds (front / back), reorganization of text info, highlighting the address of the website. three characteristics define the business card: Professional, Class, refined. The business card must be optimized for soft-touch and selective varnish printing.

Target Market(s)

Customers and Suppliers

Industry/Entity Type

Agribusiness

Contact Information for Business Card

Logo, Tél / Whatsapp, mail, url du site : alpinleaf.net

Font styles to use
Sans Serif

Requirements
Must have
• Logo of alpinleaf.net
Nice to have
• a design that stands out well on the selective varnish
Should not have
• Last name and first name

```html
<!DOCTYPE html>
<html lang="en">
<head>
<meta charset="utf-8">
<title>alpinleaf — Business Card</title>
<link href="https://fonts.googleapis.com/css2?family=Raleway:wght@600&family=Lato:wght@400&display=swap" rel="stylesheet">
<style>
  :root {
    --page: #ecebe8;
    --slate: #555759;
    --leaf: #96c462;
    --paper: #f4f4f4;
    --ink: #2a2a2a;
  }
  * { box-sizing: border-box; margin: 0; padding: 0; }
  html, body { width: 1200px; height: 900px; overflow: hidden; }
  body {
    background: var(--page);
    display: flex;
    flex-direction: column;
    align-items: center;
    justify-content: center;
    gap: 56px;
  }
  .card {
    position: relative;
    width: 560px;
    height: 362px;
    overflow: hidden;
    box-shadow: 0 2px 10px rgba(0,0,0,0.12);
  }
  .brand {
    display: flex;
    align-items: center;
    gap: 12px;
    font-family: "Raleway", sans-serif;
    font-weight: 600;
    color: var(--leaf);
    letter-spacing: 0.5px;
  }
  .brand-mark {
    display: block;
    background: var(--leaf);
  }

  /* Front */
  .card-front {
    background: var(--slate);
    display: flex;
    align-items: center;
    justify-content: center;
  }
  .card-front .brand { font-size: 52px; }
  .card-front .brand-mark { width: 30px; height: 30px; }

  /* Back */
  .card-back { background: var(--paper); }
  .card-back .wave { position: absolute; inset: 0; width: 100%; height: 100%; }
  .card-back .brand {
    position: absolute;
    top: 52px;
    right: 34px;
    font-size: 42px;
  }
  .card-back .brand-mark { width: 24px; height: 24px; }
  .contact {
    position: absolute;
    left: 44px;
    top: 178px;
    list-style: none;
    font-family: "Lato", sans-serif;
    font-size: 18px;
    color: var(--ink);
  }
  .contact li {
    display: flex;
    align-items: center;
    gap: 8px;
    height: 30px;
  }
  .contact-icon {
    width: 24px;
    height: 24px;
    background: var(--leaf);
    display: flex;
    align-items: center;
    justify-content: center;
  }
  .website {
    position: absolute;
    right: 28px;
    bottom: 88px;
    font-family: "Lato", sans-serif;
    font-size: 17px;
    color: var(--leaf);
  }
</style>
</head>
<body>

  <section class="card card-front" aria-label="Card front">
    <div class="brand"><span class="brand-mark"></span>alpinleaf</div>
  </section>

  <section class="card card-back" aria-label="Card back">
    <svg class="wave" viewBox="0 0 560 362" preserveAspectRatio="none" aria-hidden="true">
      <path d="M0,362 L0,346 C160,352 320,300 440,228 C490,198 525,184 560,180 L560,362 Z" fill="var(--slate)"/>
      <path d="M0,326 C150,336 300,300 420,228 C320,300 170,342 0,338 Z" fill="var(--leaf)"/>
    </svg>

    <div class="brand"><span class="brand-mark"></span>alpinleaf</div>

    <ul class="contact">
      <li>
        <span class="contact-icon">
          <svg width="16" height="16" viewBox="0 0 24 24" aria-hidden="true">
            <path d="M6.6 10.8a15.1 15.1 0 0 0 6.6 6.6l2.2-2.2c.3-.3.7-.4 1-.2 1.1.4 2.3.6 3.6.6.6 0 1 .4 1 1V20c0 .6-.4 1-1 1A17 17 0 0 1 3 4c0-.6.4-1 1-1h3.5c.6 0 1 .4 1 1 0 1.3.2 2.5.6 3.6.1.3 0 .7-.2 1z" fill="#fff"/>
          </svg>
        </span>
        +41 79 555 01 23
      </li>
      <li>
        <span class="contact-icon">
          <svg width="16" height="12" viewBox="0 0 16 12" aria-hidden="true">
            <rect x="0.75" y="0.75" width="14.5" height="10.5" fill="none" stroke="#fff" stroke-width="1.5"/>
            <path d="M1 1 L8 7 L15 1" fill="none" stroke="#fff" stroke-width="1.5"/>
          </svg>
        </span>
        office@alpinleaf.net
      </li>
    </ul>

    <p class="website">www.alpinleaf.net</p>
  </section>

</body>
</html>
```